Sable Grove products by Voldrin. Beauty, skin care cosmetic products

We are an all natural and organic beauty product company looking for a logo an label design ideas. Our motto is to make products that are safe, natural, in harmony with the earth and that really work. Our products will contribute to the transition from the Old Earth to the Sable Grove (as the image of the two worlds suggests). The earths can be mixed in the label. The label example is a rough sketch.
Updates

The label needs to be 1 (one) inch high and 7 inch long.

Need extra days to review

Target Market(s)

Products made with natural and organic ingredients. Beauty and skin products

Requirements
Must have
• My project must be standing out. We want customers to be draw to he product on the shelf. Wow, this label is different? what is it? All natural? I must try it.
• Must be bold but not outrageous.
• The two earth can be placed on right and left side of the tree of life on the second attachment
Nice to have
• The two Earth can be in the back ground suggesting that this product takes us from chemically and artificially filled products to something new that is in harmony with nature and health.
Should not have
• Should not be boring. Ordinary, easy to forget and ignore patterns, lettering, logos.

```html
<!DOCTYPE html>
<html lang="en">
<head>
<meta charset="utf-8">
<title>Sable Grove Products by Voldrin – Under-Arm-Balm Label</title>
<link rel="stylesheet" href="https://fonts.googleapis.com/css2?family=Cormorant+Garamond:wght@500;600&family=Open+Sans:wdth,wght@75..100,300..800&display=swap">
<style>
  :root {
    --page: #ffffff;
    --label-deep: #0b0d1c;
    --label-navy: #14183a;
    --earth-blue: #2a3590;
    --earth-glow: #3c49a8;
    --ring-green: #1f4a3a;
    --trunk-dark: #07080f;
    --text-light: #f1f1f4;
    --text-soft: #dcdce2;
    --accent-green: #8cc852;
    --accent-green-dark: #5e9e2f;
  }
  html, body {
    margin: 0;
    padding: 0;
    width: 1200px;
    height: 1067px;
    overflow: hidden;
    background: var(--page);
  }
  .canvas {
    position: relative;
    width: 1200px;
    height: 1067px;
  }
  .label {
    position: absolute;
    left: 40px;
    top: 197px;
    width: 1120px;
    height: 673px;
    overflow: hidden;
    background: linear-gradient(90deg, var(--label-deep) 0%, var(--label-navy) 62%, #1d2258 100%);
  }
  .label-art {
    position: absolute;
    inset: 0;
  }
  .side-tag {
    position: absolute;
    left: -2px;
    top: 458px;
    width: 12px;
    height: 146px;
    border: 1.5px solid var(--text-soft);
    border-left: none;
  }
  .side-tag span {
    position: absolute;
    left: -3px;
    top: 60px;
    font: 400 9px/1 "Open Sans", sans-serif;
    color: var(--text-soft);
    transform: rotate(-90deg);
    white-space: nowrap;
  }
  .scent {
    position: absolute;
    left: 60px;
    top: 326px;
    transform: translate(-50%, -50%) rotate(-90deg);
    font: 500 54px/1 "Cormorant Garamond", serif;
    letter-spacing: 11px;
    color: var(--accent-green);
    white-space: nowrap;
  }
  .brand-block {
    position: absolute;
    left: 238px;
    width: 700px;
    text-align: center;
    white-space: nowrap;
  }
  .brand-name {
    top: 102px;
    font: 500 68px/1 "Cormorant Garamond", serif;
    color: var(--text-light);
  }
  .brand-maker {
    top: 186px;
    font: 500 56px/1 "Cormorant Garamond", serif;
    color: var(--text-soft);
  }
  .brand-maker strong {
    font: 700 76px/1 "Open Sans", sans-serif;
    font-stretch: 85%;
    color: var(--text-light);
    letter-spacing: 1px;
  }
  .product-name {
    top: 320px;
    font: 700 86px/1 "Open Sans", sans-serif;
    font-stretch: 82%;
    letter-spacing: 1px;
    background: linear-gradient(90deg, var(--accent-green-dark), var(--accent-green));
    -webkit-background-clip: text;
    background-clip: text;
    color: transparent;
  }
  .claim {
    top: 484px;
    font: 500 41px/1 "Cormorant Garamond", serif;
    font-variant-numeric: lining-nums;
    color: var(--text-light);
    letter-spacing: 0.5px;
  }
  .free-from {
    top: 549px;
    font: 300 47px/1 "Open Sans", sans-serif;
    font-stretch: 76%;
    color: var(--text-soft);
  }
  .free-from b {
    font-weight: 700;
    color: var(--text-light);
  }
</style>
</head>
<body>
<div class="canvas">
  <section class="label">
    <svg class="label-art" width="1120" height="673" viewBox="0 0 1120 673">
      <defs>
        <radialGradient id="ringTone" cx="50%" cy="50%" r="50%">
          <stop offset="0%" stop-color="#0c0e22"/>
          <stop offset="70%" stop-color="#151a48"/>
          <stop offset="86%" stop-color="#1f4a3a"/>
          <stop offset="100%" stop-color="#14183a" stop-opacity="0"/>
        </radialGradient>
        <radialGradient id="earthTone" cx="50%" cy="45%" r="55%">
          <stop offset="0%" stop-color="#3c49a8"/>
          <stop offset="70%" stop-color="#2a3590"/>
          <stop offset="100%" stop-color="#1b2262" stop-opacity="0"/>
        </radialGradient>
        <linearGradient id="trunkTone" x1="0" y1="0" x2="0" y2="1">
          <stop offset="0%" stop-color="#07080f" stop-opacity="0.3"/>
          <stop offset="50%" stop-color="#07080f" stop-opacity="0.9"/>
          <stop offset="100%" stop-color="#07080f" stop-opacity="0.4"/>
        </linearGradient>
        <linearGradient id="edgeGlow" x1="0" y1="0" x2="1" y2="0">
          <stop offset="0%" stop-color="#4756b8" stop-opacity="0"/>
          <stop offset="100%" stop-color="#4f60c4" stop-opacity="0.85"/>
        </linearGradient>
      </defs>
      <g role="img" aria-label="Knotwork ring framing the scene">
        <ellipse cx="588" cy="336" rx="470" ry="470" fill="url(#ringTone)"/>
      </g>
      <g role="img" aria-label="Old Earth on the left of the tree of life">
        <ellipse cx="360" cy="336" rx="125" ry="110" fill="url(#earthTone)"/>
      </g>
      <g role="img" aria-label="Sable Grove earth on the right of the tree of life">
        <ellipse cx="805" cy="336" rx="125" ry="110" fill="url(#earthTone)"/>
      </g>
      <g role="img" aria-label="Tree of life rising between the two earths">
        <rect x="530" y="0" width="116" height="673" fill="url(#trunkTone)"/>
      </g>
      <rect x="960" y="0" width="160" height="673" fill="url(#edgeGlow)"/>
    </svg>

    <div class="side-tag"><span>4 oz</span></div>
    <div class="scent">Orignal Scent</div>

    <div class="brand-block brand-name">Sable Grove Products</div>
    <div class="brand-block brand-maker">by <strong>VOLDRIN</strong></div>
    <div class="brand-block product-name">UNDER-ARM-BALM</div>
    <div class="brand-block claim">100% NATURAL INGREDIENTS</div>
    <div class="brand-block free-from"><b>No</b> Aluminum, <b>No</b> Parabens, <b>No</b> Phthalates</div>
  </section>
</div>
</body>
</html>
```